Northmead Career Institute needs a unique tri-fold brochure design

I need a tri-fold brochure for my vocational school. We provide Nursing Assistant, Home Healthcare Aide & Phlebotomy classes at our centers and 50 programs online. The theme for our brochure and logo is Opening New Doors. I have all the text for the brochure and simples of brochures that I Like. I want the brochure to stand out and represent high quality and success. I also want the brochure to be easy to read. Yes, I'm also open to different ideas and concepts. lol
Updates

The logo and a sample of the text are now available with my brief.

Thanks,

Rob

Thanks to all the designers who took on the project and emailed me directly! If you have not replied to the invite, email me at, rkestwin47@mailnova.test

Thanks again, 
Rob 

Hello All,

Payment for the project is now GUARANTEED! Feel free to email me directly at rkestwin47@mailnova.test or you can post your first draft on my page. Fyi... full content for the brochure is only available upon request.

Thanks,

Rob

Target Market(s)

18-55 years old, but the vast majority are between the age of 24-45

Industry/Entity Type

School

Requirements
Must have
• Pictures of people in scrubs of all ages.
Should not have
• pictures of people in business wear.

```html
<!DOCTYPE html>
<html lang="en">
<head>
<meta charset="utf-8">
<title>Northmead Career Institute – Tri-fold Brochure</title>
<link rel="stylesheet" href="https://fonts.googleapis.com/css2?family=Questrial&display=swap">
<style>
  :root{
    --stage:#e4e4cc;
    --blue-deep:#0a3f86;
    --blue-mid:#1565b8;
    --blue-glow:#2f8ad8;
    --blue-light:#8fd0f5;
    --yellow:#f3e33a;
    --white:#ffffff;
    --seam:rgba(0,20,60,.35);
  }
  *{box-sizing:border-box;margin:0;padding:0}
  html,body{width:1200px;height:830px;overflow:hidden}
  body{background:var(--stage);font-family:"Questrial",sans-serif;color:var(--white);display:flex;align-items:center;justify-content:center}
  .brochure{display:flex;width:1086px;height:790px;box-shadow:0 10px 30px rgba(0,0,0,.25)}
  .panel{position:relative;width:362px;height:100%;padding:34px 30px;overflow:hidden;
    background:radial-gradient(ellipse at 60% 30%,var(--blue-glow) 0%,var(--blue-mid) 45%,var(--blue-deep) 100%)}
  .panel + .panel{border-left:1px solid var(--seam)}
  .heading-yellow{color:var(--yellow);font-size:15px;letter-spacing:.5px;text-transform:uppercase}
  .subheading{font-size:15px;text-transform:uppercase;line-height:1.25;margin-bottom:18px}
  .photo{border-radius:14px;border:6px solid var(--blue-light)}
  .photo-graduates{height:190px;background:linear-gradient(160deg,#9cc6e6,#5c7d58 55%,#1d2330);margin-bottom:24px}
  .testimonial{font-size:11.5px;line-height:1.55;text-align:justify}
  .testimonial-author{text-align:right;font-size:12px;margin:8px 0 26px}
  .panel-contact{text-align:center}
  .intro{font-size:11.5px;line-height:1.5;margin:10px 0 24px}
  .contact-title{color:var(--yellow);font-size:19px;letter-spacing:.5px;margin-bottom:6px}
  .contact-block{font-size:11.5px;line-height:1.5;margin-bottom:18px}
  .contact-block strong{font-weight:400;color:var(--yellow)}
  .panel-cover{padding:0}
  .brand{display:flex;align-items:center;justify-content:center;gap:8px;padding-top:40px;font-size:16px}
  .brand-dot{width:12px;height:12px;border-radius:50%;background:var(--white)}
  .tagline{text-align:center;margin-top:30px}
  .tagline-main{display:block;font-size:44px;color:var(--blue-light);line-height:1}
  .tagline-sub{display:block;font-size:26px;color:var(--yellow)}
  .benefits{list-style:none;margin:26px 0 0 44px;font-size:12.5px;line-height:1.9}
  .benefits li{display:flex;align-items:center;gap:7px}
  .photo-staff{position:absolute;left:0;right:0;top:470px;height:200px;
    background:linear-gradient(180deg,#2f8ad8 0%,#c9a68f 45%,#e6b9c8 75%,#1b5fae 100%)}
  .enroll{position:absolute;left:0;right:0;bottom:0;height:120px;padding:34px 30px;
    background:linear-gradient(180deg,var(--blue-mid),var(--blue-deep));color:var(--yellow);font-size:13px;line-height:1.45}
  .enroll .web{display:block}
  .enroll .phone{font-size:17px}
</style>
</head>
<body>
<main class="brochure">
  <section class="panel panel-testimonials">
    <h2 class="heading-yellow">Testimonials</h2>
    <p class="subheading">Here's what our students have to say about our classes...</p>
    <div class="photo photo-graduates" role="img" aria-label="Photo of smiling graduates in caps and gowns raising their arms"></div>
    <p class="testimonial">I inquired information from 5 different training centers before I became a HHA/CNA. The private schools wanted to charge $1000 to $1200 and told me I couldn't find a job if I did a prep course or challenge the CNA state exam. Well, I took the prep class at NCI and I passed my exam on the 1st try and I'm now working over 40 hours a week. The instructors were extremely knowledgeable, patient and willing to help. The staff were always there when needed and was very encouraging. I urge anyone to attend this training.</p>
    <p class="testimonial-author">Marcus D. Harbor City, FL</p>
    <p class="testimonial">My name is Tessa, for my CNA training I went to Northmead Career Institute. My teacher was wonderful. It was amazing. I passed my CNA state exam, with no problems. I now work with a client who is paralyzed from the waist down 4 days a week, and I am currently looking for another part-time job in elderly care. My training was wonderful! Thanks NCI :-)</p>
    <p class="testimonial-author">Tessa R. Lakeshore, FL</p>
  </section>

  <section class="panel panel-contact">
    <p class="intro">Enroll at the School that completely disregards the limitations and applies fresh and innovative methods and techniques to help you get the best of both worlds.<br><br>We are the doorway to quickly reenter the workforce for displaced workers and for individuals looking for fulfilling and rewarding long-term employment while pursuing higher education.</p>
    <h2 class="contact-title">HOW TO CONTACT US</h2>
    <div class="contact-block">
      <strong>Operation Hours:</strong><br>
      Monday through Thursday – 9am to 6pm<br>
      Friday – 9am to 5pm<br>
      Saturday – By appointment only
    </div>
    <div class="contact-block">
      <strong>Lakeshore Center</strong><br>
      4820 Willow Park Ave<br>
      Unit 210-212<br>
      Lakeshore, FL 30912<br>
      Tel: (555) 214-0190<br>
      Fax: 555-334-0177
    </div>
    <div class="contact-block">
      <strong>Brookfield Center</strong><br>
      1750 Meadowline Road<br>
      Brookfield, FL 30955<br>
      Tel: (555) 334-0142<br>
      Fax: 555-334-0177<br>
      BY APPOINTMENT ONLY
    </div>
    <div class="contact-block">
      <strong>Department Contact Information</strong><br>
      Sign up: 555-214-0190 ext 101<br>
      Customer Service: 555-214-0190 ext 102<br>
      Online Store: 555-214-0190 ext 103
    </div>
  </section>

  <section class="panel panel-cover">
    <div class="brand"><span class="brand-dot"></span>Northmead Career Institute</div>
    <h1 class="tagline"><span class="tagline-main">Opening</span><span class="tagline-sub">New Doors</span></h1>
    <ul class="benefits">
      <li><svg width="10" height="10" viewBox="0 0 10 10"><path d="M1 5l3 3 5-7" fill="none" stroke="#fff" stroke-width="1.6"/></svg>Affordable &amp; Quality Education</li>
      <li><svg width="10" height="10" viewBox="0 0 10 10"><path d="M1 5l3 3 5-7" fill="none" stroke="#fff" stroke-width="1.6"/></svg>Fast &amp; Efficient Training</li>
      <li><svg width="10" height="10" viewBox="0 0 10 10"><path d="M1 5l3 3 5-7" fill="none" stroke="#fff" stroke-width="1.6"/></svg>High Paying Jobs &amp; Rewarding Careers</li>
      <li><svg width="10" height="10" viewBox="0 0 10 10"><path d="M1 5l3 3 5-7" fill="none" stroke="#fff" stroke-width="1.6"/></svg>State Certified Caregivers &amp; Highly Rated Employers</li>
      <li><svg width="10" height="10" viewBox="0 0 10 10"><path d="M1 5l3 3 5-7" fill="none" stroke="#fff" stroke-width="1.6"/></svg>Training Facility &amp; Community</li>
    </ul>
    <div class="photo-staff" role="img" aria-label="Photo of a smiling group of healthcare workers of all ages in scrubs and white coats"></div>
    <div class="enroll">
      Enroll Online:<span class="web">northmeadcareer.test</span>
      Or Call: <span class="phone">555-214-0190</span>
    </div>
  </section>
</main>
</body>
</html>
```